Business card design for Virtual Assistance company

I need a business card designed for my virtual assistance company. We are a small company who services primarily C-level executive clients. The card needs to be double sided with the following contact information on the back:
Melissa Thornbury
Owner/CEO
info@rkpadvisory.net
www.rkpadvisory.net
555.302.9817

The front side should just have the company name incorporated: "RKP Advisory" and "virtual assistance"

The card should be simplistic, but eye catching and should speak to high level executives. Our primary focus areas consist of executive assistance and government contracting.

Target Market(s)

CEOs and executives

Contact Information for Business Card

see project description. phone, email, website.

Colors

Designer to choose only greyscale colors for use in the design.

```html
<!DOCTYPE html>
<html lang="en">
<head>
<meta charset="utf-8">
<title>RKP Advisory – Business Card</title>
<link href="https://fonts.googleapis.com/css2?family=PT+Serif:wght@400;700&family=Montserrat:wght@400;500&display=swap" rel="stylesheet">
<style>
  :root {
    --ink: #141414;
    --paper: #ffffff;
    --paper-shade: #ececec;
    --stage-light: #8a8a8a;
    --stage-dark: #2b2b2b;
    --text: #1a1a1a;
    --muted: #3a3a3a;
  }
  * { margin: 0; padding: 0; box-sizing: border-box; }
  html, body { width: 1200px; height: 900px; overflow: hidden; }
  body {
    background: radial-gradient(ellipse at 75% 20%, var(--stage-light), var(--stage-dark) 80%);
    position: relative;
    font-family: "Montserrat", sans-serif;
  }
  .card {
    position: absolute;
    width: 560px;
    height: 320px;
    border-radius: 4px;
    overflow: hidden;
    box-shadow: 0 18px 40px rgba(0,0,0,.45);
  }
  .card--front {
    left: 70px; top: 100px;
    background: var(--ink);
    display: flex; align-items: center; justify-content: center;
  }
  .front-name {
    font-family: "PT Serif", serif;
    font-weight: 400;
    font-size: 64px;
    color: var(--paper);
    letter-spacing: 1px;
  }
  .card--back {
    left: 570px; top: 480px;
    background: linear-gradient(180deg, var(--paper), var(--paper-shade));
  }
  .back-shape { position: absolute; inset: 0; }
  .company {
    position: absolute;
    left: 40px; top: 150px;
    width: 190px;
    text-align: center;
    font-family: "PT Serif", serif;
    color: var(--text);
  }
  .company-name { font-size: 27px; font-weight: 400; line-height: 1.1; }
  .company-tagline { font-size: 10.5px; letter-spacing: 1.4px; margin-top: 4px; }
  .divider {
    position: absolute;
    left: 252px; top: 95px;
    width: 1px; height: 120px;
    background: var(--muted);
  }
  .contact {
    position: absolute;
    left: 272px; top: 92px;
    color: var(--text);
  }
  .contact-name {
    font-family: "PT Serif", serif;
    font-weight: 700;
    font-size: 20px;
  }
  .contact-title { font-size: 12px; color: var(--muted); margin: 2px 0 10px 10px; }
  .contact-list { list-style: none; }
  .contact-item {
    display: flex; align-items: center; gap: 8px;
    font-size: 12.5px; line-height: 21px;
  }
  .contact-icon { width: 12px; height: 12px; fill: var(--ink); flex: none; }
</style>
</head>
<body>
  <section class="card card--front" aria-label="Card front">
    <span class="front-name">RKP Advisory</span>
  </section>

  <section class="card card--back" aria-label="Card back">
    <svg class="back-shape" viewBox="0 0 560 320" aria-hidden="true">
      <path d="M0 320 L90 320 Q420 300 560 190 L560 320 Z" fill="var(--ink)"/>
      <path d="M55 298 Q390 282 535 180 Q420 272 55 298 Z" fill="var(--ink)"/>
    </svg>

    <div class="company">
      <div class="company-name">RKP Advisory</div>
      <div class="company-tagline">VIRTUAL ASSISTANCE</div>
    </div>

    <div class="divider"></div>

    <div class="contact">
      <div class="contact-name">Melissa Thornbury</div>
      <div class="contact-title">Owner/CEO</div>
      <ul class="contact-list">
        <li class="contact-item">
          <svg class="contact-icon" viewBox="0 0 24 24"><path d="M6.6 10.8a15.1 15.1 0 0 0 6.6 6.6l2.2-2.2c.3-.3.7-.4 1-.2 1.1.4 2.3.6 3.6.6.6 0 1 .4 1 1V20c0 .6-.4 1-1 1A17 17 0 0 1 3 4c0-.6.4-1 1-1h3.5c.6 0 1 .4 1 1 0 1.3.2 2.5.6 3.6.1.3 0 .7-.2 1z"/></svg>
          555.302.9817
        </li>
        <li class="contact-item">
          <svg class="contact-icon" viewBox="0 0 24 24"><path d="M2 5h20v14H2z M2 5l10 8 10-8" /><path d="M3 6l9 7 9-7" stroke="#fff" stroke-width="1.6" fill="none"/></svg>
          info@rkpadvisory.net
        </li>
        <li class="contact-item">
          <svg class="contact-icon" viewBox="0 0 24 24"><circle cx="12" cy="12" r="10"/><path d="M2 12h20M12 2c3 3 3 17 0 20M12 2c-3 3-3 17 0 20" stroke="#fff" stroke-width="1.4" fill="none"/></svg>
          www.rkpadvisory.net
        </li>
      </ul>
    </div>
  </section>
</body>
</html>
```